Digital Billboard Design: Winter Sales Event

I own a boutique furniture store in Calgary, AB (larkhollowhome.ca) and I am looking to advertise our winter sale event on a new curved digital billboard (specs attached including required file type).

I have this billboard rented for 52-weeks so I will be looking to change the design every 4-weeks (i.e. this is intended to be an ongoing project).

The objective of this first billboard is to raise awareness around our annual winter sales event. The store itself is only a few blocks from the billboard so those commuting into downtown are just a short drive from the store.

I am looking for a fresh, clean, contemporary look that will grab your attention as you drive into downtown Calgary without presenting to much info so as to be distracting (and overwhelming -- the billboard does not need to contain all info on my current marketing material). I should also note that the store caters to a higher-end, more sophisticated clientele so the graphics need to reflect the brand (i.e. we are not Brenton Furniture or Couch Depot!).

I have attached three files:

Billboard specs
Current marketing material advertising sale (and all relevant data)
An idea that is from an American furniture store that I think is interesting

Target Market(s)

Upper middle class, sophisticated client who appreciates the finer things in life.

Industry/Entity Type

Furniture Store

Font styles to use
Sans Serif

Requirements
Must have
• Company Logo
• Winter Sales Event - 20 to 60% off
• Address: 2417 14th Ave SW
Nice to have
• Image of furniture -- see our website www.larkhollowhome.ca -- any photo from this site can be used
Should not have
• Too much text or visual distration

```html
<!DOCTYPE html>
<html lang="en">
<head>
<meta charset="utf-8">
<title>Lark Hollow Home – Winter Sales Event Billboard</title>
<link rel="stylesheet" href="https://fonts.googleapis.com/css2?family=Saira:wght@600&family=Questrial&display=swap">
<style>
  :root {
    --page-bg: #ffffff;
    --sky-blue: #82b6d3;
    --frame-blue: #5fa8cf;
    --snow-white: #ffffff;
    --ink-grey: #4a4a4c;
  }
  html, body {
    margin: 0;
    padding: 0;
    width: 1200px;
    height: 1000px;
    overflow: hidden;
    background: var(--page-bg);
  }
  .canvas {
    position: relative;
    width: 1200px;
    height: 1000px;
  }
  .billboard {
    position: absolute;
    left: 0;
    top: 0;
  }
  .headline {
    font-family: "Saira", "Arial Narrow", sans-serif;
    font-weight: 600;
    fill: var(--snow-white);
  }
  .headline--event { font-size: 60px; }
  .headline--offer { font-size: 48px; }
  .brand-name {
    font-family: "Questrial", "Helvetica", sans-serif;
    font-size: 40px;
    fill: var(--ink-grey);
  }
  .store-address {
    font-family: "Questrial", "Helvetica", sans-serif;
    font-size: 30px;
    fill: var(--ink-grey);
  }
</style>
</head>
<body>
<div class="canvas">
  <svg class="billboard" width="1200" height="1000" viewBox="0 0 1200 1000" xmlns="http://www.w3.org/2000/svg">
    <defs>
      <radialGradient id="snow-glow" cx="50%" cy="45%" r="60%">
        <stop offset="0%" stop-color="#ffffff" stop-opacity="0.45"/>
        <stop offset="100%" stop-color="#ffffff" stop-opacity="0"/>
      </radialGradient>
    </defs>

    <!-- sky band -->
    <rect class="sky-band" x="150" y="278" width="899" height="328" fill="var(--sky-blue)"/>

    <!-- snowflake cluster area -->
    <rect class="snowflake-cluster" x="860" y="292" width="146" height="230" rx="20"
          fill="url(#snow-glow)" role="img" aria-label="Cluster of five white snowflakes drifting down"/>

    <!-- sale headline -->
    <text class="headline headline--event" x="204" y="516" textLength="664" lengthAdjust="spacingAndGlyphs">WINTER SALES EVENT</text>
    <text class="headline headline--offer" x="204" y="576" textLength="450" lengthAdjust="spacingAndGlyphs">20 TO 60% OFF</text>

    <!-- store strip -->
    <rect class="store-strip" x="150" y="606" width="899" height="104" fill="var(--page-bg)"/>
    <text class="brand-name" x="576" y="652" text-anchor="middle" textLength="420" lengthAdjust="spacingAndGlyphs">LARK HOLLOW HOME</text>
    <text class="store-address" x="590" y="690" text-anchor="middle" textLength="644" lengthAdjust="spacingAndGlyphs">2417 14th Ave SW, CALGARY, AB.</text>

    <!-- frame -->
    <rect class="billboard-frame" x="150" y="278" width="899" height="432" fill="none" stroke="var(--frame-blue)" stroke-width="1.5"/>
  </svg>
</div>
</body>
</html>
```